Brightwave Reach - Business Card

We need a business card for a Social Media Marketing company that specializes in online marketing for small businesses in Canada using common Social Media platforms such as Pixlora, Chatterly, Blinkpost & Quibber.

I have uploaded a copy of our logo which I would like utilized in the business card. We would like the business card to be modern yet classy design.

Our website is www.brightwavereach.ca

Industry/Entity Type

Marketing

Contact Information for Business Card

Email: info@brightwavereach.ca
Website: www.brightwavereach.ca
Telephone: 604-555-0193

Colors

Designer to choose colors to be used in the design.

Requirements
Must have
• Social Media icons on reverse
• Please add some designs with color.

```html
<!DOCTYPE html>
<html lang="en">
<head>
<meta charset="utf-8">
<title>Brightwave Reach – Business Card</title>
<link href="https://fonts.googleapis.com/css2?family=Open+Sans:wght@400;700&display=swap" rel="stylesheet">
<style>
  :root {
    --backdrop: #2b2b2b;
    --card: #141414;
    --card-edge: #1d1d1d;
    --ink: #f2f2f2;
    --ink-soft: #bdbdbd;
    --divider: #262626;
    --accent: #d6293e;
  }
  * { box-sizing: border-box; margin: 0; padding: 0; }
  html, body { width: 1200px; height: 900px; overflow: hidden; }
  body {
    background: var(--backdrop);
    font-family: "Open Sans", Arial, sans-serif;
    color: var(--ink);
    position: relative;
  }
  .card {
    position: absolute;
    top: 305px;
    width: 510px;
    height: 290px;
    border-radius: 26px;
    background: linear-gradient(135deg, var(--card-edge), var(--card));
    box-shadow: 0 14px 30px rgba(0,0,0,.45);
    overflow: hidden;
  }
  .card--front { left: 60px; }
  .card--back { left: 630px; }

  .accent-bar {
    position: absolute;
    left: 0; right: 0; bottom: 0;
    height: 6px;
    background: var(--accent);
  }

  .brand {
    position: absolute;
    display: flex;
    align-items: center;
    gap: 10px;
  }
  .brand__dot {
    width: 12px;
    height: 12px;
    background: var(--accent);
    flex: none;
  }
  .brand__name {
    font-weight: 700;
    color: var(--ink);
    white-space: nowrap;
  }
  .card--front .brand { left: 34px; top: 134px; }
  .card--front .brand__name { font-size: 20px; }

  .card--front .divider {
    position: absolute;
    left: 262px; top: 0; bottom: 6px;
    width: 1px;
    background: var(--divider);
  }
  .contact { position: absolute; left: 290px; top: 80px; }
  .contact__name { font-size: 19px; font-weight: 400; }
  .contact__role { font-size: 12px; color: var(--ink-soft); margin-top: 1px; }
  .contact__list { list-style: none; margin-top: 40px; }
  .contact__item {
    display: flex; align-items: center; gap: 9px;
    font-size: 12.5px; line-height: 20px;
  }
  .contact__item svg { width: 11px; height: 11px; flex: none; }

  .back-texture {
    position: absolute; inset: 0;
    background: radial-gradient(ellipse at 45% 40%, #262626 0%, rgba(20,20,20,0) 60%);
  }
  .card--back .brand {
    left: 0; right: 0; top: 96px;
    justify-content: center;
  }
  .card--back .brand__name { font-size: 30px; }
  .tagline {
    position: absolute;
    left: 0; right: 0; top: 146px;
    text-align: center;
    font-size: 12px;
    color: var(--ink-soft);
  }
  .socials {
    position: absolute;
    left: 0; right: 0; top: 206px;
    display: flex;
    justify-content: center;
    gap: 22px;
    list-style: none;
  }
  .socials__item {
    display: flex; align-items: center; gap: 6px;
    font-size: 12px;
    color: var(--ink);
  }
  .socials__dot {
    width: 8px; height: 8px;
    border-radius: 50%;
    background: var(--accent);
  }
</style>
</head>
<body>
  <section class="card card--front" aria-label="Card front">
    <div class="brand">
      <span class="brand__dot"></span>
      <span class="brand__name">Brightwave Reach</span>
    </div>
    <div class="divider"></div>
    <div class="contact">
      <p class="contact__name">Marcus Hale</p>
      <p class="contact__role">Managing Director</p>
      <ul class="contact__list">
        <li class="contact__item">
          <svg viewBox="0 0 12 12"><path fill="#d6293e" d="M1 3c0-1 1-2 2-2l1.5 2.5-1 1c.6 1.3 1.7 2.4 3 3l1-1L11 8c0 1-1 2-2 2C4.6 10 1 7.4 1 3z"/></svg>
          604-555-0193
        </li>
        <li class="contact__item">
          <svg viewBox="0 0 12 12"><rect x="1" y="2.5" width="10" height="7" fill="#d6293e"/><path d="M1 2.5l5 4 5-4" stroke="#141414" stroke-width=".9" fill="none"/></svg>
          info@brightwavereach.ca
        </li>
        <li class="contact__item">
          <svg viewBox="0 0 12 12"><circle cx="6" cy="6" r="4.8" fill="none" stroke="#d6293e" stroke-width="1.2"/><path d="M1.2 6h9.6M6 1.2c2 2.6 2 7 0 9.6M6 1.2c-2 2.6-2 7 0 9.6" fill="none" stroke="#d6293e" stroke-width=".9"/></svg>
          www.brightwavereach.ca
        </li>
      </ul>
    </div>
    <div class="accent-bar"></div>
  </section>

  <section class="card card--back" aria-label="Card back">
    <div class="back-texture" role="img" aria-label="Faint distressed texture behind the brand name"></div>
    <div class="brand">
      <span class="brand__dot"></span>
      <span class="brand__name">Brightwave Reach</span>
    </div>
    <p class="tagline">Social media marketing for small business</p>
    <ul class="socials">
      <li class="socials__item"><span class="socials__dot"></span>Pixlora</li>
      <li class="socials__item"><span class="socials__dot"></span>Chatterly</li>
      <li class="socials__item"><span class="socials__dot"></span>Blinkpost</li>
      <li class="socials__item"><span class="socials__dot"></span>Quibber</li>
    </ul>
    <div class="accent-bar"></div>
  </section>
</body>
</html>
```